Business Cards - Brightpath Horizon

need to design unique business card for my mortgage business. I need to design credit card style business card for my business or any unique idea that you might have

Target Market(s)

Home Loan customers

Industry/Entity Type

Mortgage Brokerage

Contact Information for Business Card

please design credit card style or very unique style business card

Colors

Designer to choose colors to be used in the design.

Requirements
Must have
• Name
• position
• Phone number
• fax number
• email address
• website address
• social media address
• All above fields will be provided once design in finalised

```html
<!DOCTYPE html>
<html lang="en">
<head>
<meta charset="utf-8">
<title>Brightpath Horizon – Business Card</title>
<link href="https://fonts.googleapis.com/css2?family=Roboto+Slab:wght@400;700&family=Share+Tech+Mono&display=swap" rel="stylesheet">
<style>
  :root {
    --backdrop: #1d1d1d;
    --card-blue: #03abea;
    --card-blue-soft: #2cbcf0;
    --card-paper: #f1f1f1;
    --ink-white: #ffffff;
    --brand-navy: #0a3fc8;
    --brand-orange: #f7901e;
    --shadow: rgba(0,0,0,0.55);
  }
  * { box-sizing: border-box; margin: 0; padding: 0; }
  html, body { width: 1200px; height: 960px; overflow: hidden; background: var(--backdrop); }
  body { position: relative; font-family: "Roboto Slab", Georgia, serif; }

  .card {
    position: absolute;
    width: 600px;
    height: 343px;
    box-shadow: 0 3px 8px var(--shadow);
    overflow: hidden;
  }
  .card--front { left: 314px; top: 113px; background: var(--card-blue); color: var(--ink-white); }
  .card--back { left: 311px; top: 472px; background: var(--card-paper); }

  .tree-decoration {
    position: absolute; left: 0; top: 10px; width: 320px; height: 333px;
    background: radial-gradient(ellipse at 45% 40%, var(--card-blue-soft) 0%, var(--card-blue-soft) 45%, rgba(44,188,240,0) 72%);
    opacity: 0.8;
  }

  .holder { position: absolute; left: 29px; top: 33px; }
  .holder__name { font-weight: 700; font-size: 18px; line-height: 22px; }
  .holder__role { font-weight: 700; font-size: 14px; line-height: 20px; margin-top: 1px; }

  .address {
    position: absolute; right: 29px; top: 40px; text-align: right;
    font-style: normal; font-size: 13.5px; line-height: 18px;
  }

  .divider { position: absolute; left: 29px; right: 29px; top: 78px; height: 2px; background: var(--ink-white); }

  .card-number {
    position: absolute; left: 0; right: 0; top: 148px; text-align: center;
    font-family: "Share Tech Mono", "Courier New", monospace;
    font-size: 38px; line-height: 44px; letter-spacing: 2px; word-spacing: 8px;
  }

  .contact { position: absolute; left: 29px; top: 268px; font-size: 13.5px; line-height: 19px; }

  .brand-mark--front {
    position: absolute; right: 29px; top: 240px;
    display: flex; align-items: center; gap: 8px;
  }
  .brand-mark__dot { width: 22px; height: 22px; border-radius: 50%; background: var(--ink-white); flex: none; }
  .brand-mark__name { font-weight: 700; font-size: 20px; line-height: 24px; color: var(--ink-white); text-align: right; }

  .social { position: absolute; right: 23px; top: 20px; display: flex; gap: 3px; }
  .social__dot { width: 26px; height: 26px; border-radius: 50%; background: var(--brand-navy); }

  .brand-mark--back {
    position: absolute; left: 0; right: 0; top: 125px;
    display: flex; justify-content: center; align-items: center; gap: 16px;
  }
  .brand-mark--back .brand-mark__dot { width: 46px; height: 46px; background: var(--brand-orange); }
  .brand-mark--back .brand-mark__name { color: var(--brand-navy); font-size: 42px; line-height: 48px; text-align: left; }
</style>
</head>
<body>
  <section class="card card--front">
    <div class="tree-decoration" role="img" aria-label="Faint tree silhouette decoration"></div>

    <div class="holder">
      <p class="holder__name">DANIEL REYES</p>
      <p class="holder__role">CEO/FOUNDER</p>
    </div>
    <address class="address">
      2140 Cedar Hollow Drive<br>Boulder, Colorado 80302
    </address>
    <div class="divider"></div>

    <p class="card-number">555 010 1940</p>

    <div class="contact">
      <p>P. 555 013 2538</p>
      <p>daniel@brightpath.example</p>
      <p>www.brightpath.example</p>
    </div>

    <div class="brand-mark brand-mark--front">
      <span class="brand-mark__name">BRIGHTPATH<br>HORIZON</span>
      <span class="brand-mark__dot"></span>
    </div>
  </section>

  <section class="card card--back">
    <div class="social" aria-label="Social media links">
      <span class="social__dot"></span>
      <span class="social__dot"></span>
      <span class="social__dot"></span>
      <span class="social__dot"></span>
    </div>

    <div class="brand-mark brand-mark--back">
      <span class="brand-mark__dot"></span>
      <span class="brand-mark__name">BRIGHTPATH<br>HORIZON</span>
    </div>
  </section>
</body>
</html>
```